one pager for investors

I will give an initial file in any format needed. Also, the photo that must be included. As well as the logo, that must be the key to the overall design in terms of font, colors, and general layout. I will attach a file in PDF format, which is a one pager presenting a project for investors that I would like to attract and convinced to invest in my project. What I would like you to do is propose me different and better design options, taking my first draft as an example. But you must absolutely keep every single word and number, absolutely all the information written in my first draft(except “ TEMPLATE DRAFT”). Also, on the top left corner is the logo of our company, which I think should be your main inspiration document is a one pager presented to potential investors that not only has to include the most important information in order for them to be able to see everything needed to see the value of the project (which I’ve already taken care of by writing the text needed, numbers presented and timeline shown; all of which which must be preserved in terms of content, but can be completely redesigned and manipulated ) sh a.k.a. Project summary for investor to go for it.
Serious rich investors
Real eatate

```html
<!DOCTYPE html>
<html lang="fr">
<head>
<meta charset="utf-8">
<title>Verano Properties – Projet immobilier XXX</title>
<link href="https://fonts.googleapis.com/css2?family=Montserrat:wght@300;400;500;600;700;800&display=swap" rel="stylesheet">
<style>
:root{
  --backdrop:#e2e2e2;
  --paper:#ffffff;
  --brand:#3b58a0;
  --navy:#22305e;
  --row-blue:#5068a8;
  --row-grey:#ececec;
  --ink:#1c1c1c;
  --ink-soft:#333a4d;
  --sky:#9bb6ff;
  --line-light:#93aee8;
  --line-strong:#2e5de0;
}
*{margin:0;padding:0;box-sizing:border-box}
html,body{width:804px;height:1200px;overflow:hidden;background:var(--backdrop);font-family:'Montserrat',sans-serif}
.sheet{position:absolute;left:39px;top:92px;width:727px;height:940px;background:var(--paper);box-shadow:0 2px 8px rgba(0,0,0,.25);overflow:hidden}
.abs{position:absolute}
.header-block{left:364px;top:0;width:363px;height:119px;background:var(--brand)}
.header-edge{left:680px;top:0;width:47px;height:250px;background:var(--brand)}
.brand-square{left:43px;top:42px;width:64px;height:64px;border:5px solid var(--brand)}
.brand-name{left:136px;top:40px;font-size:40px;font-weight:600;letter-spacing:4px;color:var(--ink)}
.brand-sub{left:140px;top:92px;font-size:12px;font-weight:600;letter-spacing:6px;color:var(--ink)}
.confidential{left:404px;top:34px;font-size:36px;font-weight:800;color:#fff;letter-spacing:.5px}
.project-title{left:404px;top:70px;font-size:21.5px;font-weight:300;color:#fff;letter-spacing:.3px}
.photo{left:41px;top:120px;width:641px;height:255px;border:1px solid #fff;
  background:linear-gradient(180deg,#dfe1e2 0%,#cfcbc6 35%,#a98f7e 60%,#6f7a55 82%,#4f5d3a 100%)}
.desc-strip{left:0;top:362px;width:41px;height:20px;background:var(--brand)}
.desc-band{left:0;top:376px;width:681px;height:117px;background:var(--brand)}
.desc-title{left:41px;top:383px;font-size:18px;font-weight:700;letter-spacing:3.4px;color:#fff}
.desc-body{left:42px;top:406px;width:620px;font-size:11.8px;line-height:14.2px;color:#fff}
.desc-duration{left:43px;top:466px;font-size:14.4px;font-weight:700;color:#fff}
.structure-notch{left:356px;top:470px;width:0;height:0;border-right:19px solid var(--navy);border-top:22px solid transparent}
.structure{left:375px;top:470px;width:290px;height:255px;background:var(--navy);padding:24px 0 0 18px;color:#fff}
.structure h2{font-size:18px;font-weight:700;line-height:22px;margin-bottom:11px}
.structure p{font-size:11.6px;font-weight:600;line-height:14.5px;margin-left:3px}
.structure .sky{color:var(--sky)}
.structure .gap-benefit{margin-top:24px}
.structure .gap-multiple{margin-top:18px}
.structure .gap-yield{margin-top:20px}
.finance{left:41px;top:510px;width:322px}
.finance-head{height:23px;background:var(--navy);color:#fff;font-size:17px;font-weight:700;text-align:center;line-height:23px}
.finance-row{height:20px;display:flex;font-size:9.6px;color:var(--ink-soft);line-height:20px}
.finance-row .label{width:160px;padding-left:44px}
.finance-row .value{padding-left:34px}
.finance-row.grey{background:var(--row-grey)}
.finance-row.blue{background:var(--row-blue);color:#fff;font-weight:700;height:21px;line-height:21px}
.finance-row.strong{font-weight:700;color:var(--navy)}
.spacer{height:9px}
.timeline{left:0;top:750px}
.timeline text{font-family:'Montserrat',sans-serif;fill:var(--ink)}
.footer-left{left:0;top:871px;width:364px;height:69px;background:var(--navy)}
.footer-right{left:364px;top:871px;width:363px;height:69px;background:var(--brand)}
.address{left:63px;top:883px;font-size:13.2px;font-weight:700;line-height:16px;color:#fff;white-space:nowrap}
.contact{left:425px;font-size:14px;color:#fff;white-space:nowrap}
.contact.mail{top:886px}
.contact.web{top:910px;letter-spacing:2.2px}
.follow{left:581px;top:893px;font-size:9px;color:#fff}
.social{top:901px;width:15px;height:15px;border-radius:50%;background:#fff}
</style>
</head>
<body>
<div class="sheet">
  <div class="abs header-block"></div>
  <div class="abs header-edge"></div>

  <div class="abs brand-square"></div>
  <div class="abs brand-name">VERANO</div>
  <div class="abs brand-sub">PROPERTIES SA</div>

  <div class="abs confidential">CONFIDENTIEL</div>
  <div class="abs project-title">PROJET IMOBILIER “XXX”</div>

  <div class="abs photo" role="img" aria-label="Vue de la résidence de standing : immeuble de quatre niveaux avec balcons vitrés entouré d'arbres et de massifs fleuris"></div>

  <div class="abs desc-strip"></div>
  <div class="abs desc-band"></div>
  <div class="abs desc-title">DESCRIPTION DU PROJET</div>
  <p class="abs desc-body">Le projet XXX est un projet de dévloppement de 30 appartements de standing en PPE au centre de Lausanne. Le terrain a été sécurisé par la signature du vente à terme conditionnelle. L’objectif est d’obtenir le permis de construire, puis de ventre les lots. Dans un premier temps sur plan puis au fil de la construction.</p>
  <div class="abs desc-duration">Durée estimée du projet – 24 à 36 mois.</div>

  <div class="abs structure-notch"></div>
  <section class="abs structure">
    <h2>STRUCTURE<br>D’INVESTISSEMENT</h2>
    <p class="sky">Besoin de fonds propres CHF 2’000’000</p>
    <p class="sky">Retour de fonds total CHF 3’156’600</p>
    <p class="gap-benefit">Bénéfice net investisseur CHF 1’656’600</p>
    <p class="sky">Soit 2/3 du bénéfice projet</p>
    <p class="gap-multiple">Multiple sur fonds propres x1.83</p>
    <p class="gap-yield">Rendement annualisé 41.4%</p>
    <p class="sky">Calcul sur 24 mois</p>
  </section>

  <section class="abs finance">
    <div class="finance-head">PLAN FINANCIER</div>
    <div class="finance-row grey"><span class="label">Prix du terrain</span><span class="value">CHF 2’000’000</span></div>
    <div class="finance-row"><span class="label">Frais d’acquisition</span><span class="value">CHF 100’000</span></div>
    <div class="finance-row grey"><span class="label">Coût de construction</span><span class="value">CHF 2’500’000</span></div>
    <div class="finance-row"><span class="label">Divers &amp; imprévus</span><span class="value">CHF200’000</span></div>
    <div class="finance-row blue"><span class="label">Prix de revient total</span><span class="value">CHF 4’800’000</span></div>
    <div class="spacer"></div>
    <div class="finance-row blue"><span class="label">Prix de vente total</span><span class="value">CHF 7’500’000</span></div>
    <div class="finance-row grey"><span class="label">Honoraires sur vente</span><span class="value">CHF 190’000</span></div>
    <div class="spacer"></div>
    <div class="finance-row blue"><span class="label">Marge projet</span><span class="value">CHF 2’510’000</span></div>
    <div class="finance-row grey strong"><span class="label">En % sur prix de vente</span><span class="value">33.47%</span></div>
  </section>

  <svg class="abs timeline" width="727" height="115" viewBox="0 0 727 115">
    <rect x="40" y="52" width="158" height="6" fill="#93aee8"/>
    <rect x="198" y="52" width="158" height="6" fill="#2e5de0"/>
    <rect x="356" y="52" width="158" height="6" fill="#93aee8"/>
    <rect x="514" y="52" width="160" height="6" fill="#2e5de0"/>
    <polygon points="673,50 681,55 673,60" fill="#2e5de0"/>
    <line x1="122" y1="27" x2="122" y2="52" stroke="#93aee8" stroke-width="1"/>
    <circle cx="122" cy="27" r="3.5" fill="#93aee8"/>
    <line x1="436" y1="27" x2="436" y2="52" stroke="#93aee8" stroke-width="1"/>
    <circle cx="436" cy="27" r="3.5" fill="#93aee8"/>
    <line x1="277" y1="58" x2="277" y2="85" stroke="#2e5de0" stroke-width="1.2"/>
    <circle cx="277" cy="85" r="3.5" fill="#2e5de0"/>
    <line x1="594" y1="58" x2="594" y2="85" stroke="#2e5de0" stroke-width="1.2"/>
    <circle cx="594" cy="85" r="3.5" fill="#2e5de0"/>
    <text x="95" y="16" font-size="11.8" font-weight="700">08.2024</text>
    <text x="406" y="16" font-size="11.8" font-weight="700">12.2025</text>
    <text x="249" y="106" font-size="11.8" font-weight="700">04.2025</text>
    <text x="569" y="106" font-size="11.8" font-weight="700">12.2025</text>
    <text x="228" y="41" font-size="11.8">Mise à l’enquête</text>
    <text x="566" y="43" font-size="11.8">Livraison</text>
    <text x="81" y="78" font-size="11.8">Achat parcelle</text>
    <text x="378" y="79" font-size="11.8">Début construction</text>
  </svg>

  <div class="abs footer-left"></div>
  <div class="abs footer-right"></div>
  <svg class="abs" style="left:40px;top:898px" width="16" height="18" viewBox="0 0 16 18" aria-hidden="true">
    <path d="M8 1a6.5 6.5 0 0 1 6.5 6.5C14.5 12 8 17 8 17S1.5 12 1.5 7.5A6.5 6.5 0 0 1 8 1z" fill="#fff"/>
    <circle cx="8" cy="7.3" r="2.5" fill="#22305e"/>
  </svg>
  <div class="abs address">Verano Properties Vaud SA -<br>Chemin des Pins4-CH-1000 Lausanne</div>

  <svg class="abs" style="left:404px;top:888px" width="17" height="17" viewBox="0 0 17 17" aria-hidden="true">
    <circle cx="8.5" cy="8.5" r="7.8" fill="none" stroke="#fff" stroke-width="1.3"/>
    <rect x="4.6" y="5.8" width="7.8" height="5.6" fill="none" stroke="#fff" stroke-width="1"/>
    <polyline points="4.6,5.8 8.5,9 12.4,5.8" fill="none" stroke="#fff" stroke-width="1"/>
  </svg>
  <div class="abs contact mail">info@verano.ch</div>
  <svg class="abs" style="left:404px;top:912px" width="17" height="17" viewBox="0 0 17 17" aria-hidden="true">
    <circle cx="8.5" cy="8.5" r="7.8" fill="none" stroke="#fff" stroke-width="1.3"/>
    <ellipse cx="8.5" cy="8.5" rx="3.2" ry="7" fill="none" stroke="#fff" stroke-width=".9"/>
    <line x1="1.5" y1="8.5" x2="15.5" y2="8.5" stroke="#fff" stroke-width=".9"/>
  </svg>
  <div class="abs contact web">www.verano.ch</div>

  <div class="abs follow">follow us</div>
  <div class="abs social" style="left:582px;top:900px"></div>
  <div class="abs social" style="left:604px;top:900px"></div>
  <div class="abs social" style="left:627px;top:900px"></div>
</div>
</body>
</html>
```